IT’S NOT A CLEANING, IT’S YOUR LIFE! TOP TEN REASONS WHY THIS IS NOT JUST A “CLEANING”

We made a list for our patients to let them know why our hygiene appointments are different than other cleanings. Since this is a lot of information, we would like it easily readable within 4-5 feet but we do not want the post to be HUGE. Please see below:

IT’S NOT A CLEANING, IT’S YOUR LIFE!
TOP TEN REASONS WHY THIS IS NOT JUST A “CLEANING”

10. We make you look better. Healthy teeth and gums are more attractive. Recent studies
show that the smile is the first thing people notice and that people with better looking teeth
are more confident and successful.

9. We can relieve your headaches. During your hygiene visit we evaluate for serious bite
issues, many of which lead to muscle soreness, headaches, and migraines.

8. We check for oral cancer. Oral cancer kills 1 person per hour 24 hours a day. The death rate for oral cancer is higher than cancers we routinely hear about such as cervical, thyroid and skin cancer.

7. We make you smell better. During your hygiene visit we eliminate many of the germs that live under your gum tissue and cause bad breath.

6. We save you money. By utilizing the latest dental technology (digital x-rays, mouth
cameras, and magnification glasses) we can help with early detection of tooth and gum
problems and save you the cost of gum surgery, root canals, and implants.

5. We clean in places you cannot. We clean under the gum line and between teeth where
most of the germs hide and cause dental disease. 40% of the bacteria in your mouth lives in
between your teeth.

4. We prevent pain. We identify tooth decay that can lead to nerve involvement and pain,
root canal, and tooth loss.

3. We save your teeth. Most tooth loss is from periodontal/gum disease. At each visit we
evaluate the health of your gums and bone with our periodontal screening. Periodontal
disease, like high blood pressure, is symptomless until it is in advanced stages.

2. We protect your loved ones. Studies have proven that the bacteria that cause dental
disease can be transmitted from person to person. Think about that the next time you kiss
someone!

1. We prolong life. Researchers have linked the inflammation and infection found in the
mouth to heart attacks, strokes, and Alzheimer’s. By reducing infection in your mouth we can
greatly improve your overall health!

```html
<!DOCTYPE html>
<html lang="en">
<head>
<meta charset="UTF-8">
<title>It's Not a Cleaning, It's Your Life!</title>
<link rel="stylesheet" href="https://fonts.googleapis.com/css2?family=Roboto:wght@400&family=Roboto+Condensed:wght@400&display=swap">
<style>
  :root {
    --page-bg: #ece7e2;
    --paper: #ffffff;
    --peach: #f8c5a6;
    --peach-light: #fbdccb;
    --band: #fdeee6;
    --headline-red: #d0665a;
    --headline-dark: #4a3b36;
    --body-text: #6a4a3e;
    --badge: #ffffff;
    --badge-text: #e0957a;
    --photo-light: #f6efe9;
    --photo-warm: #e9cdb8;
  }
  * { box-sizing: border-box; margin: 0; padding: 0; }
  html, body { width: 890px; height: 1200px; overflow: hidden; }
  body { background: var(--page-bg); position: relative; }

  .poster {
    position: absolute;
    left: 78px;
    top: 33px;
    width: 612px;
    height: 945px;
    transform: scale(1.2);
    transform-origin: top left;
    background: var(--paper);
    overflow: hidden;
    box-shadow: 0 2px 8px rgba(0,0,0,0.15);
  }

  .photo-person {
    position: absolute;
    left: 0; top: 0;
    width: 390px; height: 440px;
    background: radial-gradient(ellipse at 40% 35%, var(--photo-warm) 0%, var(--photo-light) 55%, var(--paper) 100%);
  }
  .photo-model {
    position: absolute;
    left: 390px; top: 232px;
    width: 215px; height: 208px;
    background: linear-gradient(160deg, var(--photo-warm) 0%, var(--photo-light) 70%);
  }

  .headline {
    position: absolute;
    left: 285px; top: 87px;
    font-family: "Roboto", Arial, sans-serif;
    font-weight: 400;
    font-size: 23px;
    line-height: 23.5px;
    text-transform: uppercase;
    color: var(--headline-red);
    letter-spacing: 0.2px;
  }
  .headline .dark { color: var(--headline-dark); }

  .wave {
    position: absolute;
    left: 0; top: 0;
    width: 612px; height: 945px;
  }

  .reasons {
    position: absolute;
    left: 64px; top: 512px;
    width: 490px;
    list-style: none;
    display: flex;
    flex-direction: column;
    gap: 10px;
    font-family: "Roboto Condensed", "Arial Narrow", sans-serif;
    font-size: 10.3px;
    line-height: 14px;
    color: var(--body-text);
  }
  .reason { display: flex; align-items: flex-start; }
  .reason-number {
    flex: 0 0 12px;
    width: 12px; height: 12px;
    margin-top: 1px;
    margin-right: 11px;
    border-radius: 50%;
    background: var(--badge);
    color: var(--badge-text);
    font-size: 7.5px;
    line-height: 12px;
    text-align: center;
  }
  .reason-text { flex: 1; }
</style>
</head>
<body>
  <div class="poster">
    <div class="photo-person" role="img" aria-label="Smiling dental hygienist in a white coat holding a large toothbrush"></div>
    <div class="photo-model" role="img" aria-label="Hand holding a large dental model of teeth and gums"></div>

    <h1 class="headline">
      It’s not a cleaning,<br>
      it’s your life!<br>
      <span class="dark">Top ten reasons</span><br>
      why this is<br>
      not just a “cleaning”
    </h1>

    <svg class="wave" viewBox="0 0 612 945" aria-hidden="true">
      <path d="M0 392 C160 366 360 392 612 438 L612 945 L0 945 Z" fill="var(--peach)"/>
      <path d="M0 386 C170 360 380 385 612 432 L612 444 C380 398 170 374 0 398 Z" fill="var(--peach-light)"/>
      <path d="M0 424 C190 404 400 428 612 462 L612 505 C400 468 190 440 0 456 Z" fill="var(--band)"/>
    </svg>

    <ol class="reasons">
      <li class="reason"><span class="reason-number">10</span><span class="reason-text">We make you look better. Healthy teeth and gums are more attractive. Recent studies show that the smile is the first thing people notice and that people with better looking teeth are more confident and successful.</span></li>
      <li class="reason"><span class="reason-number">9</span><span class="reason-text">We can relieve your headaches. During your hygiene visit we evaluate for serious bite issues, many of which lead to muscle soreness, headaches, and migraines.</span></li>
      <li class="reason"><span class="reason-number">8</span><span class="reason-text">We check for oral cancer. Oral cancer kills 1 person per hour 24 hours a day. The death rate for oral cancer is higher than cancers we routinely hear about such as cervical, thyroid and skin cancer.</span></li>
      <li class="reason"><span class="reason-number">7</span><span class="reason-text">We make you smell better. During your hygiene visit we eliminate many of the germs that live under your gum tissue and cause bad breath.</span></li>
      <li class="reason"><span class="reason-number">6</span><span class="reason-text">We save you money. By utilizing the latest dental technology (digital x-rays, mouth cameras, and magnification glasses) we can help with early detection of tooth and gum problems and save you the cost of gum surgery, root canals, and implants.</span></li>
      <li class="reason"><span class="reason-number">5</span><span class="reason-text">We clean in places you cannot. We clean under the gum line and between teeth where most of the germs hide and cause dental disease. 40% of the bacteria in your mouth lives in between your teeth.</span></li>
      <li class="reason"><span class="reason-number">4</span><span class="reason-text">We prevent pain. We identify tooth decay that can lead to nerve involvement and pain, root canal, and tooth loss.</span></li>
      <li class="reason"><span class="reason-number">3</span><span class="reason-text">We save your teeth. Most tooth loss is from periodontal/gum disease. At each visit we evaluate the health of your gums and bone with our periodontal screening. Periodontal disease, like high blood pressure, is symptomless until it is in advanced stages.</span></li>
      <li class="reason"><span class="reason-number">2</span><span class="reason-text">We protect your loved ones. Studies have proven that the bacteria that cause dental disease can be transmitted from person to person. Think about that the next time you kiss someone!</span></li>
      <li class="reason"><span class="reason-number">1</span><span class="reason-text">We prolong life. Researchers have linked the inflammation and infection found in the mouth to heart attacks, strokes, and Alzheimer’s. By reducing infection in your mouth we can greatly improve your overall health!</span></li>
    </ol>
  </div>
</body>
</html>
```